Hull Harbour Trade Website makeover

Hull Harbour Trade is in need of a makeover. It is feeling tired and needs a fresh new look and feel as well as being user friendly.

Hull Harbour Trade is an industry owned marketplace website for the sale of recreational boats, marina berths, chandlery, water craft like kayaks - anything related to recreation on the water. The main focus however is boats - new and used. The site is only available to industry businesses so no private sales are available on the site.

This approach ensures that the buyers know that title is guaranteed to all boats sold and that the businesses are reputable and stand behind their products.

The current site address is www.hullharbourtrade.com.au

Target Market(s)

The target market are people interested in outdoor recreation - boaters, kayakers, sailors, paddle boarders, those looking for marina berths for their boat and those looking for service providers.

It should appeal to families, males and females, sports oriented people, fishermen, and those just looking for a relaxing, outdoor, healthy lifestyle.

Requirements
Must have
• Be very user friendly, intuitive in terms of searching, be uncluttered, fresh and engaging.
• Marine recreation is about lifestyle, fun and relaxation. When people buy a boat they are buying into a desirable, healthy lifestyle.
• It must present as professional and give consumers confidence about the professionalism of the businesses selling their products on the site.
Nice to have
• Good images that portray the lifestyle in the Australian marketplace.
• Cater for the needs of sellers to be able to showcase their products to consumers.
Should not have
• Be cluttered and hard to navigate.

```html
<!DOCTYPE html>
<html lang="en">
<head>
<meta charset="utf-8">
<title>Hull Harbour Trade</title>
<link href="https://fonts.googleapis.com/css2?family=Open+Sans:wght@400;600;700&display=swap" rel="stylesheet">
<style>
:root{
  --navy:#0d3a66;
  --blue:#0a5bad;
  --nav-top:#1478c8;
  --nav-bottom:#0a4f96;
  --panel:#92c5ec;
  --heading:#2a7bbd;
  --text:#444;
  --white:#fff;
  --button:#0d3f80;
  --map-tone:#2f5f8e;
}
*{box-sizing:border-box;margin:0;padding:0}
html,body{width:717px;height:1200px;overflow:hidden;background:var(--white)}
body{font-family:"Open Sans",Arial,sans-serif;color:var(--text)}
.page{position:relative;width:717px;height:1200px;overflow:hidden}
.abs{position:absolute}
.brand{left:78px;top:22px;font-size:15px;font-weight:700;color:var(--blue);display:flex;align-items:center;gap:6px}
.brand-square{width:12px;height:12px;background:var(--blue)}
.social{top:39px;width:21px;height:21px;border-radius:50%;background:var(--navy)}
.nav{left:0;top:65px;width:717px;height:34px;background:linear-gradient(var(--nav-top),var(--nav-bottom));display:flex;padding-left:80px}
.nav a{color:var(--white);font-size:7.6px;font-weight:600;text-decoration:none;text-align:center;display:flex;align-items:center;justify-content:center;line-height:1.3;white-space:nowrap;border-right:1px solid rgba(255,255,255,.25);padding:0 2px}
.nav a:last-child{border-right:none}
.hero{left:0;top:99px;width:717px;height:274px;background:linear-gradient(180deg,#8fa8b8 0%,#d9a77a 35%,#6b7f8c 62%,#2d4a63 100%)}
.caption{left:78px;top:266px;width:274px;height:81px;background:var(--navy);color:var(--white);font-size:13px;font-weight:400;line-height:1.45;padding:20px 13px}
.search{left:362px;top:118px;width:275px;height:247px;background:var(--panel);font-size:7px;color:#2f4a66}
.search h2{position:absolute;left:14px;top:12px;font-size:12.5px;font-weight:700;color:#184c8c}
.field{position:absolute;background:var(--white);border:1px solid #c8dced;height:18px;font-size:6px;color:#aaa;padding:5px 6px}
.select::after{content:"";position:absolute;right:3px;top:4px;width:8px;height:8px;border:1px solid #888}
.btn{position:absolute;background:var(--button);color:var(--white);font-size:7px;text-align:center;line-height:18px;border-radius:1px}
.lbl{position:absolute;font-size:7px;color:#3a4a5a;white-space:nowrap}
.map{left:8px;top:182px;width:44px;height:40px;background:var(--map-tone);opacity:.45;border-radius:6px}
.checks{position:absolute;left:74px;top:227px;font-size:6px;display:flex;gap:4px;align-items:center;color:#333}
.box{display:inline-block;width:7px;height:7px;border:1px solid #888;background:#fff;vertical-align:middle;margin-right:1px}
.alert-band{left:0;top:373px;width:717px;height:50px;background:var(--blue);color:var(--white)}
.alert-band h3{position:absolute;left:76px;top:5px;font-size:9.5px;font-weight:400;color:#bfe0ff}
.alert-band p{position:absolute;left:76px;top:22px;width:380px;font-size:6.8px;line-height:1.6}
.alert-band p span{color:#bfe0ff}
.alert-btn{left:478px;top:384px;width:160px;height:28px;background:#8cc0ea;color:var(--white);font-size:10px;text-align:center;line-height:28px;border-radius:2px}
.section-title{left:78px;font-size:9.3px;font-weight:700;color:var(--heading);text-transform:uppercase}
.copy{left:78px;width:418px;font-size:6px;line-height:14.4px;color:var(--text)}
.ad{left:520px;width:107px}
.news-arrow{top:847px;width:24px;height:20px}
.news{left:78px;top:867px;width:418px;height:140px;background:var(--navy);color:var(--white);padding:10px 34px;font-size:6px;line-height:14.4px}
.news h4{font-size:7.4px;font-weight:700;margin-top:4px}
.news .item+.item{margin-top:18px}
.partners{left:78px;top:1032px;width:560px;height:44px;display:flex;justify-content:space-between;align-items:center}
.partner{background:#dfe8f2}
.footer{left:0;top:1093px;width:717px;height:107px;background:var(--blue);color:var(--white);text-align:center}
.footer .links{font-size:5.8px;line-height:12px;padding-top:12px}
.footer .menu{font-size:7.2px;margin-top:13px;word-spacing:2px}
.footer .copyright{font-size:7.2px;margin-top:11px}
</style>
</head>
<body>
<div class="page">

  <header>
    <div class="abs brand"><span class="brand-square"></span>Hull Harbour Trade</div>
    <span class="abs social" style="left:592px"></span>
    <span class="abs social" style="left:617px"></span>
  </header>

  <nav class="abs nav">
    <a style="width:26px">Home</a>
    <a style="width:88px">New Boats<br>Marine Accessories</a>
    <a style="width:84px">Marine<br>Products &amp; Services</a>
    <a style="width:77px">Accredited<br>Brokers &amp; Dealers</a>
    <a style="width:64px">Hull Harbour<br>Trade Members</a>
    <a style="width:75px">Marinas &amp; Berths</a>
    <a style="width:56px">Useful Links</a>
    <a style="width:47px">About Us</a>
    <a style="width:47px">Contact Us</a>
  </nav>

  <section class="abs hero" role="img" aria-label="Marina at sunset with moored motor yachts and city buildings"></section>
  <svg class="abs" style="left:50px;top:206px" width="22" height="34" viewBox="0 0 22 34"><polyline points="18,2 4,17 18,32" fill="none" stroke="rgba(255,255,255,.7)" stroke-width="3"/></svg>
  <svg class="abs" style="left:645px;top:206px" width="22" height="34" viewBox="0 0 22 34"><polyline points="4,2 18,17 4,32" fill="none" stroke="rgba(255,255,255,.7)" stroke-width="3"/></svg>

  <div class="abs caption">WE only have RMG members listings<br>so that YOU can buy with confidence!</div>

  <form class="abs search">
    <h2>New and Used Boats for Sale</h2>
    <span class="lbl" style="left:16px;top:36px">Quick Search</span>
    <span class="field" style="left:13px;top:48px;width:123px">Search</span>
    <span class="field" style="left:140px;top:48px;width:50px">All Words</span>
    <span class="btn" style="left:195px;top:48px;width:64px">Quick Search</span>
    <span class="lbl" style="left:0;width:275px;text-align:center;top:74px">OR Select your state/s, a price range and new/used</span>
    <span class="lbl" style="left:0;width:72px;text-align:right;top:100px">New and/or Used</span>
    <span class="field select" style="left:81px;top:96px;width:178px">Search</span>
    <span class="lbl" style="left:0;width:72px;text-align:right;top:127px">Price from</span>
    <span class="field select" style="left:81px;top:123px;width:178px">0</span>
    <span class="lbl" style="left:0;width:72px;text-align:right;top:151px">Price to</span>
    <span class="field select" style="left:81px;top:147px;width:178px">All</span>
    <span class="btn" style="left:216px;top:170px;width:43px">Search</span>
    <div class="abs map" role="img" aria-label="Map of Australia"></div>
    <span class="lbl" style="left:124px;top:196px">or for more options</span>
    <span class="btn" style="left:194px;top:192px;width:65px">Advanced Search</span>
    <div class="checks">Select All
      <span><i class="box"></i>QLD</span><span><i class="box"></i>NSW</span><span><i class="box"></i>VIC</span><span><i class="box"></i>TAS</span><span><i class="box"></i>SA</span><span><i class="box"></i>NT</span><span><i class="box"></i>WA</span>
    </div>
  </form>

  <section class="abs alert-band">
    <h3>Want us to do the searching for you?</h3>
    <p><span>Register now!</span> We can email you when boats are listed that match your criteria.We can also alert our members with what you are looking for. Its that easy!</p>
  </section>
  <div class="abs alert-btn">Register for e-mail Alerts</div>

  <main>
    <h2 class="abs section-title" style="top:459px">Boats for sale backed by the Recreational Marine Guild</h2>
    <p class="abs copy" style="top:485px">The Recreational Marine Guilds and their network of members welcome you to the only marine marketplace website offering the largest range of boats for sale and other marine related products, backed by the association quality assurance programs.<br>When you deal with the professionals of the marine industry you are assured of highest possible standard of service and product quality. All marine industry members are bound by the code of conduct and ethics, set down by their Industry Association.<br>HullHarbourTrade.com.au is owned and operated by the Recreational Marine Guilds of Australia and offers the consumer the benefit of making their purchase with the utmost confidence, from expert marine focused members, offering quality products and service.</p>

    <h2 class="abs section-title" style="top:609px">Buy with confidence</h2>
    <p class="abs copy" style="top:637px">You have come to the right place: HullHarbourTrade.com.au offers all types of boats for sale including fishing boats, power boats, sailing boats, catamarans, trimarans, monohulls, mulithulls, trailer sailers, cruisers, super yachts and boat shares.<br>There are new and used boats for sale by Accredited Boat Brokers and Dealers from across Australia. Boat for Sale listings are updated by the seller making Hull Harbour Trade the up-to-date source of information for the boat buyer. With inventory info and lots of photos, Hull Harbour Trade is the best-referenced boat sales site on the net.</p>

    <h2 class="abs section-title" style="top:737px">Types of boats for sale in Australia</h2>
    <p class="abs copy" style="top:751px">Boating is an popular pastime enjoyed by many Australians along the vast coastline, inland lakes, rivers and creeks. The entire coast of the country is ideal for deep water Power Boats and Yachts, and the sheltered bays and inlets are perfectly suited to fishing boats and smaller sailing boats and power boats.Hull Harbour Trade caters for all interests when it is time to Research, Discover and Experience the boating lifestyle. There are all types of Power Boats, Fishing Boats, Yachts, Ski Boats, Speed Boats, House Boats New and Used, offered for sale by Recreational Marine Guild Members throughout Australia.</p>

    <h2 class="abs section-title" style="top:851px;left:77px">Latest News &amp; Events</h2>
    <svg class="abs news-arrow" style="left:444px" viewBox="0 0 24 20"><rect width="24" height="20" fill="#2a7bbd"/><polyline points="14,5 9,10 14,15" fill="none" stroke="#fff" stroke-width="2"/></svg>
    <svg class="abs news-arrow" style="left:472px" viewBox="0 0 24 20"><rect width="24" height="20" fill="#0d3a66"/><polyline points="10,5 15,10 10,15" fill="none" stroke="#fff" stroke-width="2"/></svg>
    <div class="abs news">
      <div class="item">
        <h4>2013-12-01 Coastal Daily</h4>
        Fisherman catch bag of firearms at Coombabah boat ramp, Gold Coast<br>
        FISHERMEN have hauled a bag containing firearms from a popular angling spot on the Gold Coast.
      </div>
      <div class="item">
        <h4>2013-11-29 Riverside Herald</h4>
        Getting involved in cleaning up Moreton Bay<br>
        Politicians, rugby players and community groups will all grab a bag and start picking up the rubbish for the Cleaning up the Bay Initiative around Moreton Bay this Sunday.
      </div>
    </div>
  </main>

  <aside>
    <div class="abs ad" style="top:442px;height:89px;background:linear-gradient(#f6b545,#3a8fd0)" role="img" aria-label="Advert: Twinhull Co power catamaran builder"></div>
    <div class="abs ad" style="top:536px;height:90px;background:linear-gradient(#f07a22 30%,#1d5aa6 30%,#3b8c4a)" role="img" aria-label="Advert: Shoreline Motorcraft new and used boats, 07 5500 0142"></div>
    <div class="abs ad" style="top:631px;height:100px;background:linear-gradient(#eef2f6 60%,#0d3a7a 60%)" role="img" aria-label="Advert: Anchor Point Sales boat sales and boat gear, 07 5500 0387"></div>
    <div class="abs ad" style="top:735px;height:89px;background:linear-gradient(#2a5f92,#0a4e9e)" role="img" aria-label="Advert: Keel &amp; Co Marine used boat specialists, (07) 3800 0915"></div>
    <div class="abs ad" style="top:829px;height:178px;background:linear-gradient(#8ba6b8,#0b54a8 40%,#0a4c9a)" role="img" aria-label="Advert: beware, things you need to know before you buy an imported boat or engine"></div>
  </aside>

  <div class="abs partners" role="img" aria-label="Partner and association badges">
    <span class="partner" style="width:52px;height:36px"></span>
    <span class="partner" style="width:86px;height:28px"></span>
    <span class="partner" style="width:26px;height:38px"></span>
    <span class="partner" style="width:86px;height:30px"></span>
    <span class="partner" style="width:42px;height:40px"></span>
    <span class="partner" style="width:56px;height:36px"></span>
    <span class="partner" style="width:43px;height:37px"></span>
    <span class="partner" style="width:50px;height:34px"></span>
  </div>

  <footer class="abs footer">
    <div class="links">
      Boats for Sale Australia: Sydney Boats for Sale • Brisbane Boats for Sale • Gold Coast Boats for Sale • Melbourne Boats for Sale • Perth Boats for Sale • Adelaide Boats • Tasmania Boats<br>
      Type of Boats for Sale: Power Boats for Sale • Sail Boats for Sale • Luxury Boats for Sale • House Boats for Sale • Fishing Boats for Sale • Yachts for Sale<br>
      Popular Boat Sale Brands: Coralline Boats for Sale • Baymark Boats for Sale • Kestrel Craft Boats for Sale • Seabreeze Boats for Sale • Bowline Boats for Sale • Tidewell Boats for Sale
    </div>
    <div class="menu">Home &nbsp;|&nbsp; About Us &nbsp;|&nbsp; Products &nbsp;|&nbsp; FAQ's &nbsp;|&nbsp; Tetimonials &nbsp;|&nbsp; Terma &amp; Conditions &nbsp;|&nbsp; Privacy Policy &nbsp;|&nbsp;Contact Us</div>
    <div class="copyright">© 2013 Company Name ,All Rights Reserved</div>
  </footer>

</div>
</body>
</html>
```